Modern Verdell Tree Care Website

I need a website for a full service Tree Care company. The company provides tree pruning, tree removal, tree preservation, emergency services, stump grinding, and emergency tree services.

Target Market(s)

Customers that need tree services

Industry/Entity Type

Landscaping, Tree Services

Coding

Coded - Design and coding required

Number of Pages Required

5+ page

Font styles to use
Sans Serif

Requirements
Must have
• Good clean design that showcases the services the company provides.
Nice to have
• Services page; contact form, blog, home page, about page

```html
<!DOCTYPE html>
<html lang="en">
<head>
<meta charset="utf-8">
<title>Verdell Tree Care</title>
<link href="https://fonts.googleapis.com/css2?family=League+Spartan:wght@500;600;700&family=Montserrat:wght@400;500;600;700&display=swap" rel="stylesheet">
<style>
:root{
  --green:#78b82a;
  --green-dark:#5f9a1c;
  --orange:#f8a532;
  --ink:#2f2f2f;
  --body:#4a4a4a;
  --cream:#f2f1ea;
  --line:#e3c9a6;
  --white:#ffffff;
}
*{margin:0;padding:0;box-sizing:border-box}
html,body{width:1200px;height:4815px;overflow:hidden}
body{position:relative;background:var(--white);font-family:"Montserrat",sans-serif;color:var(--body)}
.abs{position:absolute}
.head-font{font-family:"League Spartan",sans-serif}
.ph{position:absolute}

/* header */
.site-header{left:0;top:0;width:1200px;height:84px;background:var(--white)}
.brand{left:96px;top:14px;display:flex;align-items:center;gap:12px}
.brand-mark{width:44px;height:44px;background:var(--green)}
.brand-name{font-family:"League Spartan",sans-serif;font-weight:700;font-size:27px;color:var(--green);letter-spacing:1px;line-height:1}
.main-nav{left:340px;top:30px;display:flex;gap:0;font-size:13px;font-weight:600;letter-spacing:1.5px;color:var(--ink)}
.main-nav span{padding:0 32px;border-left:1px solid #bbb}
.main-nav span:first-child{border-left:none;padding-left:0;color:var(--green);border-bottom:2px solid var(--green);padding-bottom:8px}
.phone-box{left:978px;top:0;width:222px;height:84px;background:var(--green);color:var(--white);display:flex;align-items:center;gap:12px;padding-left:22px;font-size:15px;font-weight:600;line-height:1.35}
.phone-box .ico{width:26px;height:26px;border-radius:50%;background:var(--white);display:flex;align-items:center;justify-content:center}

/* hero */
.hero-photo{left:0;top:84px;width:1200px;height:640px;background:linear-gradient(180deg,#b8d4ee 0%,#dbe8f3 55%,#eef2f4 100%)}
.hero-tree{left:520px;top:84px;width:680px;height:620px;background:linear-gradient(135deg,#a07d5a,#6d8c3a 60%,#8aa456);clip-path:polygon(30% 0,100% 0,100% 100%,10% 100%,45% 40%)}
.hero-kicker{left:100px;top:240px;font-size:17px;color:var(--ink);letter-spacing:.5px}
.hero-title{left:96px;top:266px;font-family:"League Spartan",sans-serif;font-weight:600;font-size:38px;letter-spacing:2px;color:var(--ink);line-height:47px}
.hero-title .hl{background:var(--green);color:var(--white);padding:0 8px}
.hero-sub{left:100px;top:366px;font-size:18px;color:var(--ink)}
.btn{background:var(--orange);color:var(--white);font-size:14px;font-weight:700;letter-spacing:1px;display:flex;align-items:center;justify-content:center}
.hero-btn{left:94px;top:414px;width:165px;height:42px}

/* about */
.about-block{left:0;top:725px;width:340px;height:565px;background:var(--green)}
.about-photo{left:136px;top:809px;width:404px;height:402px;background:linear-gradient(160deg,#9fc66a,#4f7e2a 55%,#e9973a 80%,#5d8a33);clip-path:polygon(0 0,100% 0,100% 100%,0 100%)}
.about-title{left:604px;top:812px;font-family:"League Spartan",sans-serif;font-weight:600;font-size:38px;letter-spacing:2px;line-height:42px;color:var(--ink)}
.about-title em{font-style:normal;color:var(--green)}
.about-rule{left:920px;top:872px;width:280px;height:1px;background:var(--orange)}
.about-rule::before{content:"";position:absolute;left:-4px;top:-4px;width:9px;height:9px;border-radius:50%;background:var(--orange)}
.about-text{left:613px;top:916px;width:510px;font-size:15px;line-height:23px;color:var(--body)}
.about-text p+p{margin-top:23px}
.about-btn{left:614px;top:1152px;width:152px;height:42px}

/* section titles */
.sec-title{width:1200px;left:0;text-align:center;font-family:"League Spartan",sans-serif;font-weight:600;font-size:38px;letter-spacing:2px;color:var(--ink)}
.sec-title em{font-style:normal;color:var(--green)}
.tri{width:0;height:0;border-left:11px solid transparent;border-right:11px solid transparent;border-bottom:20px solid var(--green)}

/* services */
.services-bg{left:0;top:1346px;width:1200px;height:785px;background:var(--cream)}
.service{width:329px}
.service .shot{height:206px}
.service .label{position:absolute;left:0;top:206px;display:flex;align-items:flex-start;gap:14px}
.service .badge{width:64px;height:64px;border-radius:50%;background:var(--green);border:5px solid var(--white);margin-top:-30px;margin-left:20px;display:flex;align-items:center;justify-content:center;flex:none}
.service .name{font-family:"League Spartan",sans-serif;font-weight:600;font-size:20px;letter-spacing:1px;color:var(--ink);margin-top:10px;line-height:22px}
.service .overlay{position:absolute;left:36px;top:50px;width:270px;font-size:11.5px;line-height:19px;color:var(--white)}

/* why choose */
.diamond{width:175px;height:175px;transform:rotate(45deg);border:1.5px solid var(--line);background:var(--white)}
.diamond.active{background:var(--orange);border-color:var(--orange)}
.why-item{width:220px;text-align:center;font-size:14px;font-weight:600;color:var(--ink);letter-spacing:.3px;line-height:19px}
.why-item.active{color:var(--white)}
.why-item svg{display:block;margin:0 auto 10px}

/* blogs */
.blogs-bg{left:0;top:2700px;width:1200px;height:648px;background:var(--cream)}
.blog-card{background:var(--white);border:1px solid #d9d9d9}
.date{background:var(--green);color:var(--white);font-size:11px;font-weight:700;letter-spacing:.5px;display:inline-block}
.blog-title{font-weight:700;color:var(--ink)}
.more{color:var(--green);font-weight:700;text-decoration:underline;letter-spacing:.5px}

/* testimonials */
.testi-title{left:105px;top:3480px;font-family:"League Spartan",sans-serif;font-weight:600;font-size:28px;letter-spacing:2px;line-height:32px;color:var(--ink)}
.quote-card{width:330px;height:330px;border-radius:50%;background:var(--white);box-shadow:0 0 24px rgba(0,0,0,.09);text-align:center;padding:48px 42px 0}
.quote-mark{font-family:"League Spartan",sans-serif;font-size:70px;line-height:50px;color:var(--orange);font-weight:700;height:40px}
.quote-text{font-size:13px;line-height:23px;color:var(--body);margin-top:6px}
.quote-name{font-size:15px;font-weight:700;color:var(--ink);margin-top:8px}
.stars{color:var(--orange);font-size:20px;letter-spacing:1px}
.arrow{font-size:30px;color:var(--green);font-weight:400}

/* contact */
.contact-bottom{left:0;top:4355px;width:1200px;height:125px;background:var(--cream)}
.contact-box{left:135px;top:3975px;width:942px;height:505px;background:linear-gradient(180deg,#7dbb30,#6fae25);border-radius:14px}
.field{background:var(--white);font-size:13px;color:#555;display:flex;align-items:center;gap:10px;padding-left:22px}
.field.msg{align-items:flex-start;padding-top:18px}
.send-btn{left:510px;top:4377px;width:180px;height:41px;background:#1e3d1a;color:var(--white);font-size:13px;font-weight:700;letter-spacing:1px;display:flex;align-items:center;justify-content:center}

/* footer */
.foot-head{font-family:"League Spartan",sans-serif;font-weight:600;font-size:19px;letter-spacing:1px;color:var(--ink);border-left:2px solid var(--green);padding-left:14px}
.foot-list{font-size:13px;line-height:29px;color:var(--ink);font-weight:500}
.foot-small{font-size:13px;color:var(--ink);line-height:20px}
.social{width:28px;height:28px;border-radius:50%;border:2px solid var(--orange)}
</style>
</head>
<body>

<!-- Header -->
<header class="abs site-header">
  <div class="abs brand">
    <div class="brand-mark"></div>
    <div class="brand-name">VERDELL<br>TREE CARE</div>
  </div>
  <nav class="abs main-nav">
    <span>HOME</span><span>ABOUT US</span><span>SERVICES</span><span>BLOG</span><span>CONTACT US</span>
  </nav>
  <div class="abs phone-box">
    <div class="ico"><svg width="14" height="14" viewBox="0 0 24 24"><path d="M6.6 10.8a15.2 15.2 0 0 0 6.6 6.6l2.2-2.2a1 1 0 0 1 1-.25 11.4 11.4 0 0 0 3.6.6 1 1 0 0 1 1 1V20a1 1 0 0 1-1 1A17 17 0 0 1 3 4a1 1 0 0 1 1-1h3.5a1 1 0 0 1 1 1c0 1.25.2 2.45.6 3.6a1 1 0 0 1-.25 1z" fill="#78b82a"/></svg></div>
    <div>(555) 214-7730<br>(555) 386-1142</div>
  </div>
</header>

<!-- Hero -->
<section>
  <div class="ph hero-photo" role="img" aria-label="Arborist with a chainsaw cutting large tree limbs against a blue sky"></div>
  <div class="ph hero-tree" role="img" aria-label="Crossed tree trunks being removed by a climbing arborist"></div>
  <p class="abs hero-kicker">WELCOME TO VERDELL TREE CARE</p>
  <h1 class="abs hero-title">VERDELL FOR ALL YOUR<br><span class="hl">TREE CARE</span>NEEDS</h1>
  <p class="abs hero-sub">Serving Brookfield and surrounding areas.</p>
  <div class="abs btn hero-btn">CONTACT US</div>
  <svg class="abs" style="left:0;top:660px" width="1200" height="100" viewBox="0 0 1200 100" preserveAspectRatio="none">
    <polygon points="0,0 1200,40 1200,100 0,100" fill="#ffffff"/>
    <polygon points="250,12 1200,40 1200,62" fill="#78b82a"/>
  </svg>
</section>

<!-- About -->
<section>
  <div class="abs about-block"></div>
  <div class="ph about-photo" role="img" aria-label="Arborist in an orange shirt climbing a tree, framed in a large letter shape"></div>
  <h2 class="abs about-title">ABOUT VERDELL<br><em>TREE CARE</em></h2>
  <div class="abs tri" style="left:844px;top:856px"></div>
  <div class="abs about-rule"></div>
  <div class="abs about-text">
    <p>At Verdell Tree Care, we are more than just a tree service company, we are stewards of our beautiful trees. With a passion deeply rooted in arboriculture, we embark on a mission to promote the health, beauty, and safety of your trees and landscapes.</p>
    <p>Whether it's expert tree trimming to enhance aesthetics, meticulous tree removal to mitigate hazards, or comprehensive tree health assessments to ensure safety , we approach each task with unwavering dedication and attention to detail.</p>
  </div>
  <div class="abs btn about-btn">LEARN MORE</div>
</section>

<!-- Services -->
<section>
  <div class="abs services-bg"></div>
  <svg class="abs" style="left:0;top:1318px" width="1200" height="70" viewBox="0 0 1200 70" preserveAspectRatio="none">
    <polygon points="0,0 1200,0 1200,28 0,28" fill="#ffffff"/>
    <polygon points="0,40 850,10 0,70" fill="#f8a532"/>
  </svg>
  <div class="abs tri" style="left:589px;top:1384px"></div>
  <h2 class="abs sec-title" style="top:1418px">OUR <em>SERVICES</em></h2>

  <div class="abs service" style="left:86px;top:1491px">
    <div class="ph shot" style="position:relative;background:linear-gradient(135deg,#8aa860,#b4a57a 50%,#d9602c 75%,#6c8c4a)" role="img" aria-label="Pruning shears cutting a tree branch"></div>
    <div class="label"><div class="badge"><svg width="26" height="26" viewBox="0 0 24 24" fill="none" stroke="#fff" stroke-width="2"><circle cx="6" cy="18" r="3"/><path d="M8 16 20 4M9 13l4 4"/></svg></div><div class="name">TREE PRUNING</div></div>
  </div>
  <div class="abs service" style="left:431px;top:1491px">
    <div class="ph shot" style="position:relative;background:linear-gradient(135deg,#3d3526,#5e5238 60%,#2f2a1f)" role="img" aria-label="Tree trunk being cut for removal"></div>
    <p class="overlay">Lorem ipsum dolor sit amet, consectetur adipiscing elit, sed do eiusmod tempor incididunt ut labore et dolore magna aliqua. Quis ipsum suspendisse ultrices gravida. Risus commodo viverra maecenas</p>
    <div class="label"><div class="badge" style="background:var(--orange)"><svg width="26" height="26" viewBox="0 0 24 24" fill="none" stroke="#fff" stroke-width="2"><path d="M4 20h16M7 20V9h10v11M10 9V5h4v4"/></svg></div><div class="name">TREE REMOVAL</div></div>
  </div>
  <div class="abs service" style="left:779px;top:1491px">
    <div class="ph shot" style="position:relative;background:linear-gradient(135deg,#6e4a32,#8c6447 50%,#5c8a3a)" role="img" aria-label="Shovel digging soil around a young tree"></div>
    <div class="label"><div class="badge"><svg width="26" height="26" viewBox="0 0 24 24" fill="none" stroke="#fff" stroke-width="2"><path d="M12 3l8 3v6c0 5-4 8-8 9-4-1-8-4-8-9V6z"/><path d="M12 8v9"/></svg></div><div class="name">TREE PRESERVATION</div></div>
  </div>

  <div class="abs service" style="left:89px;top:1776px">
    <div class="ph shot" style="position:relative;background:linear-gradient(135deg,#8a5a3c,#c9a36a 50%,#e7a52a 70%,#9b7a55)" role="img" aria-label="Stump grinding machine at work"></div>
    <div class="label"><div class="badge"><svg width="26" height="26" viewBox="0 0 24 24" fill="none" stroke="#fff" stroke-width="2"><circle cx="12" cy="12" r="7"/><circle cx="12" cy="12" r="2"/></svg></div><div class="name">STUMP GRINDING</div></div>
  </div>
  <div class="abs service" style="left:434px;top:1776px">
    <div class="ph shot" style="position:relative;background:linear-gradient(135deg,#6c8a4a,#a8b48c 50%,#5f7a3c)" role="img" aria-label="Storm-fallen tree resting on a house"></div>
    <div class="label"><div class="badge"><svg width="26" height="26" viewBox="0 0 24 24" fill="none" stroke="#fff" stroke-width="2"><path d="M6 20 18 4M10 10l-4-2M13 13l4 1"/></svg></div><div class="name">TREE EMERGENCY<br>SERVICES</div></div>
  </div>
  <div class="abs service" style="left:782px;top:1776px">
    <div class="ph shot" style="position:relative;background:linear-gradient(135deg,#5c9ad0,#7aa850 55%,#e58b3a 75%,#4e7a33)" role="img" aria-label="Arborist climbing a tree with ropes for cabling"></div>
    <div class="label"><div class="badge"><svg width="26" height="26" viewBox="0 0 24 24" fill="none" stroke="#fff" stroke-width="2"><path d="M12 21V9M12 9c-4 0-6-3-6-5 3 0 6 2 6 5zm0 0c4 0 6-3 6-5-3 0-6 2-6 5M6 14h12"/></svg></div><div class="name">CABLING &amp; BRACING</div></div>
  </div>
</section>

<!-- Why choose us -->
<section>
  <div class="abs tri" style="left:597px;top:2163px"></div>
  <h2 class="abs sec-title" style="top:2196px">WHY <em>CHOOSE US</em></h2>

  <div class="abs diamond" style="left:111px;top:2305px"></div>
  <div class="abs diamond active" style="left:375px;top:2305px"></div>
  <div class="abs diamond" style="left:638px;top:2305px"></div>
  <div class="abs diamond" style="left:904px;top:2305px"></div>
  <div class="abs diamond" style="left:244px;top:2445px"></div>
  <div class="abs diamond" style="left:507px;top:2445px"></div>
  <div class="abs diamond" style="left:771px;top:2445px"></div>

  <div class="abs why-item" style="left:88px;top:2328px"><svg width="44" height="44" viewBox="0 0 24 24" fill="none" stroke="#78b82a" stroke-width="1.4"><rect x="5" y="3" width="14" height="18"/><path d="M8 8h8M8 12h8M9 16l2 2 4-4"/></svg>LICENSED AND<br>INSURED</div>
  <div class="abs why-item active" style="left:352px;top:2328px"><svg width="44" height="44" viewBox="0 0 24 24" fill="none" stroke="#fff" stroke-width="1.4"><circle cx="12" cy="9" r="6"/><path d="M12 15v6M9 21h6"/></svg>PROFESSIONAL<br>WORK</div>
  <div class="abs why-item" style="left:615px;top:2328px"><svg width="44" height="44" viewBox="0 0 24 24" fill="none" stroke="#78b82a" stroke-width="1.4"><path d="M12 21s-6-6-6-11a6 6 0 0 1 12 0c0 5-6 11-6 11z"/><circle cx="12" cy="10" r="2"/></svg>LOCALLY OWNED<br>&amp; OPERATED</div>
  <div class="abs why-item" style="left:881px;top:2328px"><svg width="44" height="44" viewBox="0 0 24 24" fill="none" stroke="#78b82a" stroke-width="1.4"><rect x="5" y="3" width="14" height="18"/><path d="M8 7h8M8 11h8M8 15h5"/></svg>FREE ESTIMATE</div>
  <div class="abs why-item" style="left:221px;top:2466px"><svg width="44" height="44" viewBox="0 0 24 24" fill="none" stroke="#78b82a" stroke-width="1.4"><circle cx="12" cy="12" r="8"/><path d="M12 7v5l3 2"/></svg>24 HOUR EMERGENCY<br>SERVICES</div>
  <div class="abs why-item" style="left:484px;top:2466px"><svg width="44" height="44" viewBox="0 0 24 24" fill="none" stroke="#78b82a" stroke-width="1.4"><path d="M6 10a6 6 0 0 1 12 0zM4 10h16M7 21c0-3 2-5 5-5s5 2 5 5"/></svg>SAFETY IS OUR<br>TOP PRIORITY</div>
  <div class="abs why-item" style="left:748px;top:2466px"><svg width="44" height="44" viewBox="0 0 24 24" fill="none" stroke="#78b82a" stroke-width="1.4"><circle cx="12" cy="7" r="3"/><circle cx="5" cy="10" r="2"/><circle cx="19" cy="10" r="2"/><path d="M6 20c0-4 3-7 6-7s6 3 6 7M2 19c0-3 1-5 3-5M22 19c0-3-1-5-3-5"/></svg>LICENSED ARBORIST<br>ON STAFF</div>
</section>

<!-- Blogs -->
<section>
  <div class="abs blogs-bg"></div>
  <svg class="abs" style="left:0;top:2676px" width="1200" height="72" viewBox="0 0 1200 72" preserveAspectRatio="none">
    <polygon points="0,0 1000,52 0,36" fill="#f8a532"/>
  </svg>
  <div class="abs tri" style="left:585px;top:2753px"></div>
  <h2 class="abs sec-title" style="top:2790px">LATEST <em>BLOGS</em></h2>

  <div class="abs blog-card" style="left:105px;top:2878px;width:474px;height:406px">
    <div class="ph" style="left:0;top:0;width:472px;height:285px;background:linear-gradient(135deg,#4a5a3a,#8a8478 45%,#d64a2a 60%,#5b6a48)" role="img" aria-label="Chainsaw cutting into a large tree trunk"></div>
    <span class="abs date" style="left:0;top:257px;padding:8px 22px">20 MAY 2024</span>
    <p class="abs blog-title" style="left:38px;top:310px;width:400px;font-size:17px;line-height:26px">Lorem ipsum dolor sit amet consectetur adipiscing elit sed do eiusmod</p>
    <span class="abs more" style="left:38px;top:368px;font-size:13px">LEARN MORE</span>
  </div>

  <div class="abs blog-card" style="left:600px;top:2878px;width:501px;height:193px">
    <div class="ph" style="left:0;top:0;width:234px;height:191px;background:linear-gradient(135deg,#7e8a6a,#c6c4b4 55%,#5c6e40)" role="img" aria-label="Arborist climbing with harness and ropes"></div>
    <span class="abs date" style="left:258px;top:40px;padding:5px 12px;font-size:9px">20 MAY 2024</span>
    <p class="abs blog-title" style="left:262px;top:72px;width:215px;font-size:13.5px;line-height:20px">Lorem ipsum dolor sit amet consectetur adipiscing elit sed do eiusmod</p>
    <span class="abs more" style="left:262px;top:138px;font-size:11px">LEARN MORE</span>
  </div>

  <div class="abs blog-card" style="left:600px;top:3089px;width:501px;height:195px">
    <div class="ph" style="left:0;top:0;width:234px;height:193px;background:linear-gradient(135deg,#6c8a48,#b8c29a 50%,#4e6a34)" role="img" aria-label="Worker using long-handled pruners in a tree"></div>
    <span class="abs date" style="left:262px;top:40px;padding:5px 12px;font-size:9px">10 MAY 2024</span>
    <p class="abs blog-title" style="left:266px;top:72px;width:215px;font-size:13.5px;line-height:20px">Lorem ipsum dolor sit amet consectetur adipiscing elit sed do eiusmod</p>
    <span class="abs more" style="left:266px;top:138px;font-size:11px">LEARN MORE</span>
  </div>
</section>

<!-- Testimonials -->
<section>
  <svg class="abs" style="left:0;top:3345px" width="1200" height="90" viewBox="0 0 1200 90" preserveAspectRatio="none">
    <polygon points="0,0 1200,0 1200,28" fill="#f2f1ea"/>
    <polygon points="140,12 1200,28 1200,80" fill="#78b82a"/>
  </svg>
  <h2 class="abs testi-title">WHAT PEOPLE ARE<br>SAYING ABOUT US</h2>
  <div class="abs tri" style="left:387px;top:3513px"></div>
  <div class="ph" style="left:69px;top:3560px;width:370px;height:328px;background:radial-gradient(ellipse at 50% 40%,#5f9a2a 0%,#3f7a1c 55%,rgba(255,255,255,0) 72%)" role="img" aria-label="Large green deciduous tree"></div>

  <span class="abs arrow" style="left:407px;top:3618px">&#8249;</span>
  <span class="abs arrow" style="left:1124px;top:3618px">&#8250;</span>

  <div class="abs quote-card" style="left:437px;top:3480px">
    <div class="quote-mark">&ldquo;</div>
    <p class="quote-text">"Lorem ipsum dolor sit amet, consectetur adipiscing elit, sed do eiusmod tempor incididunt ut labore et dolore magna aliqua Quis ipsum suspendisse ultrices gravida Risus commodo viverra maecenas "</p>
    <p class="quote-name">Daniel Harlow</p>
    <div class="stars">★★★★★</div>
  </div>
  <div class="abs quote-card" style="left:783px;top:3480px">
    <div class="quote-mark">&ldquo;</div>
    <p class="quote-text">"Lorem ipsum dolor sit amet, consectetur adipiscing elit, sed do eiusmod tempor incididunt ut labore et dolore magna aliqua Quis ipsum suspendisse ultrices gravida Risus commodo viverra maecenas "</p>
    <p class="quote-name">Daniel Harlow</p>
    <div class="stars">★★★★★</div>
  </div>
  <div class="abs quote-card" style="left:1150px;top:3480px"></div>
</section>

<!-- Contact -->
<section>
  <div class="abs contact-bottom"></div>
  <div class="abs contact-box"></div>
  <div class="abs tri" style="left:592px;top:4003px;border-bottom-color:#fff"></div>
  <h2 class="abs sec-title" style="top:4042px;color:#fff">CONTACT US</h2>
  <div class="abs field" style="left:260px;top:4103px;width:338px;height:56px">&#128100; First Name*</div>
  <div class="abs field" style="left:611px;top:4103px;width:340px;height:56px">&#128100; Last Name*</div>
  <div class="abs field" style="left:260px;top:4168px;width:338px;height:56px">&#9993; Email address</div>
  <div class="abs field" style="left:611px;top:4168px;width:340px;height:56px">&#9742; Phone number</div>
  <div class="abs field msg" style="left:260px;top:4239px;width:691px;height:116px">&#128172; Leave Message</div>
  <div class="abs send-btn">SEND MESSAGE</div>
</section>

<!-- Footer -->
<footer>
  <div class="abs brand" style="left:120px;top:4570px">
    <div class="brand-mark" style="width:52px;height:52px"></div>
    <div class="brand-name" style="font-size:32px">VERDELL<br>TREE CARE</div>
  </div>
  <p class="abs foot-small" style="left:123px;top:4658px;font-size:12px">Copyright © 2024 Verdell Tree Care<br>All Right Reserved</p>

  <h4 class="abs foot-head" style="left:428px;top:4552px">NAVIGATION</h4>
  <div class="abs foot-list" style="left:444px;top:4590px"><span style="text-decoration:underline">Home</span><br>About Us<br>Services<br>Blogs<br>Contact</div>

  <h4 class="abs foot-head" style="left:650px;top:4552px">CONTACT US</h4>
  <svg class="abs" style="left:666px;top:4600px" width="28" height="28" viewBox="0 0 24 24" fill="none" stroke="#777" stroke-width="1.4"><path d="M6.6 10.8a15.2 15.2 0 0 0 6.6 6.6l2.2-2.2a1 1 0 0 1 1-.25 11.4 11.4 0 0 0 3.6.6 1 1 0 0 1 1 1V20a1 1 0 0 1-1 1A17 17 0 0 1 3 4a1 1 0 0 1 1-1h3.5a1 1 0 0 1 1 1c0 1.25.2 2.45.6 3.6a1 1 0 0 1-.25 1z"/></svg>
  <p class="abs foot-small" style="left:706px;top:4592px;font-size:12px;line-height:17px">Phone number<br><b>(555) 214-7730<br>(555) 386-1142</b></p>
  <svg class="abs" style="left:666px;top:4668px" width="28" height="22" viewBox="0 0 24 18" fill="none" stroke="#777" stroke-width="1.4"><rect x="1" y="1" width="22" height="16"/><path d="M1 1l11 9 11-9"/></svg>
  <p class="abs foot-small" style="left:708px;top:4664px;font-size:12px;line-height:17px">Email address<br><b>hello@verdelltreecare.com</b></p>

  <h4 class="abs foot-head" style="left:922px;top:4552px">FOLLOW US</h4>
  <div class="abs social" style="left:940px;top:4596px"></div>
  <div class="abs social" style="left:979px;top:4596px"></div>
  <div class="abs social" style="left:1018px;top:4596px"></div>
  <div class="abs social" style="left:1057px;top:4596px"></div>
</footer>

</body>
</html>
```